Aquatic View

We need a web design for a new window cleaning company name Tidewell Glass Care. We are located in Grand Cayman, Cayman Islands. We are a small company, a team of husband and wife. Our services include residencial interior and exterior window cleaning and commercial. Extra services such as ceiling fans cleaning, mirrors, high dusting. Home cleaning services. Power washing. Explaining the service. We want a modern, beachy style with aquatic colors. We want to use our domain name "tidewellglasscare.ky". We want to portray a clean, modern and professional design.

Target Market(s)

Big Home owners

Industry/Entity Type

Cleaning Service

Contact Information for Business Card

Company Name: Tidewell Glass Care
Name: Desmond Farrowby owner/manager
Phone: 345-9170452
Email: desmond@tidewellglasscare.ky
Website: tidewellglasscare.ky
Address: P.O.Box 2486 GT, George Town, Grand Cayman KY1-1203 Cayman Islands

Number of Pages Required

2 page

Font styles to use
Sans Serif

Colors
0592cd
0455a3
33a6d7
85cae6
cadf82
abd036
fbf289

Requirements
Nice to have
• Pictures of an ocean view and palm trees from clear windows.
• https://quorvantel.com/bidlinker/
• Use the above for "free estimate".

```html
<!DOCTYPE html>
<html lang="en">
<head>
<meta charset="utf-8">
<title>Tidewell Glass Care</title>
<link rel="stylesheet" href="https://fonts.googleapis.com/css2?family=Roboto:wght@300;400;500;700&family=Oswald:wght@400;500&family=Open+Sans:wght@400;600&display=swap">
<style>
:root{
  --ocean:#0592cd;
  --deep:#0455a3;
  --sky:#33a6d7;
  --foam:#85cae6;
  --ink:#333333;
  --muted:#777777;
  --card:#f0f4f6;
  --line:#d6dde1;
  --night:#1c1c1c;
  --night-deep:#121212;
  --white:#ffffff;
}
*{box-sizing:border-box;margin:0;padding:0}
html,body{width:1200px;height:2314px;overflow:hidden}
body{position:relative;background:var(--white);font-family:"Roboto",Arial,sans-serif;color:var(--ink)}
.abs{position:absolute}

.topbar{left:0;top:0;width:1200px;height:38px;background:var(--ocean);color:var(--white);font-size:12px}
.topbar span{position:absolute;top:12px}

.header{left:0;top:38px;width:1200px;height:96px;background:var(--white)}
.brand{left:102px;top:34px;display:flex;align-items:center;gap:10px;font-size:18px;font-weight:700;color:var(--deep)}
.brand i{display:block;width:22px;height:22px;border-radius:50%;background:var(--ocean)}
.nav{right:98px;top:38px;display:flex;align-items:center;font-size:13px;font-weight:500;text-transform:uppercase}
.nav a{color:var(--ink);text-decoration:none;padding:0 16px}
.nav a.active{color:var(--ocean)}
.nav .slash{width:1px;height:30px;background:#bbb;transform:rotate(28deg)}

.hero{left:0;top:134px;width:1200px;height:532px;background:linear-gradient(180deg,#1f7fd0 0%,#4fa6e4 42%,#8ccdec 58%,#2fb4c9 66%,#3aa1b9 74%,#e9dcc0 84%,#d6c19a 100%)}
.hero-title{left:0;top:488px;width:1200px;text-align:center;font-family:"Oswald",Arial,sans-serif;font-size:34px;font-weight:500;color:var(--deep)}
.search{left:353px;top:551px;width:494px;height:44px;background:var(--white);display:flex}
.search span{flex:1;padding:15px 20px;font-size:12px;color:#888}
.search b{width:85px;background:#1a1a1a;color:var(--white);font-size:12px;font-weight:500;display:flex;align-items:center;justify-content:center}
.slider-arrows{left:565px;top:617px;width:70px;height:28px;background:var(--white);border:1px solid #ccc;border-radius:14px}

.section-title{left:0;width:1200px;text-align:center;font-size:26px;font-weight:500;text-transform:uppercase;color:var(--ink)}
.intro{left:200px;top:760px;width:800px;text-align:center;font-size:12px;line-height:21px;color:var(--muted)}
.down{left:586px;top:814px;width:28px;height:38px;border:1px solid #aac;border-radius:5px}

.card{width:314px;height:402px;top:861px}
.card svg{position:absolute;left:0;top:0}
.card .card-title{position:absolute;left:0;top:57px;width:314px;text-align:center;color:var(--white);font-size:18px;font-weight:400;text-transform:uppercase}
.card .icon{position:absolute;left:112px;top:124px;width:90px;height:90px}
.card p{position:absolute;left:22px;top:238px;width:270px;text-align:center;font-size:12px;line-height:20px;color:#444}
.btn{display:flex;align-items:center;justify-content:center;background:var(--deep);color:var(--white);font-size:12px;font-weight:700;text-transform:uppercase;border-radius:4px}
.card .btn{position:absolute;left:110px;top:337px;width:97px;height:36px}

.about-title{left:99px;top:1318px;font-size:26px;font-weight:500;text-transform:uppercase}
.about-text{left:99px;top:1370px;width:512px;font-size:12px;line-height:21.4px;color:#555}
.about-btn{left:99px;top:1536px;width:91px;height:36px}
.video{left:651px;top:1327px;width:449px;height:243px;background:linear-gradient(135deg,#5d6f78 0%,#8c979b 45%,#4e5a60 100%)}
.play{left:188px;top:84px;width:76px;height:76px;border-radius:50%;background:rgba(255,255,255,.9)}

.gallery-item{top:1706px;height:210px;border:3px solid #f2f2f2}
.g1{left:99px;width:324px;background:linear-gradient(160deg,#dfe8ef,#8fb1cc 50%,#e8eef2)}
.g2{left:444px;width:321px;background:linear-gradient(180deg,#f2f2f2 0%,#e3e3e3 45%,#7a3a22 62%,#4a2416 100%)}
.g3{left:774px;width:324px;background:linear-gradient(180deg,#bfd7ea 0%,#e9eef1 55%,#d7d0c5 100%)}

.footer{left:0;top:1976px;width:1200px;height:294px;background:var(--night);font-family:"Open Sans",Arial,sans-serif;color:#ccc}
.footer h4{position:absolute;top:64px;font-size:19px;font-weight:600;color:var(--white);text-transform:uppercase}
.footer ul{list-style:none;position:absolute;font-size:14px;line-height:24px}
.footer .divider{position:absolute;top:63px;width:1px;height:182px;background:#3a3a3a}
.footer .fine{position:absolute;font-size:12px;line-height:22px;color:#ccc}
.nl-input{left:611px;top:173px;width:233px;height:34px;background:var(--white);font-size:12px;font-style:italic;color:#777;padding:10px 12px}
.nl-go{left:844px;top:173px;width:46px;height:34px;background:var(--ocean);color:var(--white);font-size:12px;font-weight:600;display:flex;align-items:center;justify-content:center}
.social li{display:flex;align-items:center;gap:12px;height:31px;font-size:14px}
.social li i{display:block;width:10px;height:10px;background:var(--sky)}
.bottombar{left:0;top:2270px;width:1200px;height:44px;background:var(--night-deep);font-family:"Open Sans",Arial,sans-serif;font-size:12px;color:#777;padding:15px 99px}
</style>
</head>
<body>

<div class="abs topbar">
  <span style="left:98px">USD ($) &#9662;</span>
  <span style="left:183px">English &#9662;</span>
  <span style="left:922px">? Help</span>
  <span style="left:996px;font-weight:500">&#9679; Log in / Register</span>
</div>

<header class="abs header">
  <div class="abs brand"><i></i>Tidewell Glass Care</div>
  <nav class="abs nav">
    <a class="active">Home</a><span class="slash"></span>
    <a>About Us</a><span class="slash"></span>
    <a>Services</a><span class="slash"></span>
    <a>Gallery</a><span class="slash"></span>
    <a>Contacts</a>
  </nav>
</header>

<section class="abs hero" role="img" aria-label="Tropical beach with a leaning palm tree, turquoise sea and blue sky"></section>
<h1 class="abs hero-title">CLEANING IN CAYMAN ISLANDS</h1>
<div class="abs search"><span>Search For Your Text</span><b>Let's Go!</b></div>
<div class="abs slider-arrows">
  <svg width="70" height="28" viewBox="0 0 70 28"><path d="M25 9l-5 5 5 5M45 9l5 5-5 5" fill="none" stroke="#111" stroke-width="2"/></svg>
</div>

<h2 class="abs section-title" style="top:712px">Welcome to Tidewell Glass Care</h2>
<p class="abs intro">There are many variations of passages of Lorem Ipsum available, but the majority have suffered alteration in some form, by injected humour, or randomised words which don't look even slightly believable. If you are going to use a passage of Lorem Ipsum.</p>
<div class="abs down"><svg width="26" height="36" viewBox="0 0 26 36"><path d="M13 10v15M8 20l5 6 5-6" fill="none" stroke="var(--deep)" stroke-width="2"/></svg></div>

<article class="abs card" style="left:99px">
  <svg width="314" height="402" viewBox="0 0 314 402">
    <path d="M0.5 152V3 Q160 12 313.5 28V401.5H0.5Z" fill="var(--card)" stroke="var(--line)"/>
    <path d="M0 3 Q160 12 314 28V152H0Z" fill="var(--ocean)"/>
  </svg>
  <h3 class="card-title">Window Cleaning</h3>
  <svg class="icon" viewBox="0 0 90 90"><g fill="none" stroke="#222" stroke-width="3"><rect x="8" y="12" width="74" height="66"/><path d="M8 12l18 8v50l-18 8M26 20h40v50H26"/></g></svg>
  <p>Doloremque laudantium, totam rem aperiam, eaqu quae ab illo inventore veritatis et quasi architecto beatae vitae dicta sunt explicabo. Nemo ipsam voluptatem quia voluptas.</p>
  <span class="btn">Read More</span>
</article>

<article class="abs card" style="left:443px">
  <svg width="314" height="402" viewBox="0 0 314 402">
    <path d="M0.5 152V28 Q157 36 313.5 28V401.5H0.5Z" fill="var(--card)" stroke="var(--line)"/>
    <path d="M0 28 Q157 36 314 28V152H0Z" fill="var(--ocean)"/>
  </svg>
  <h3 class="card-title">Ceiling Fans Cleaning</h3>
  <svg class="icon" viewBox="0 0 90 90"><g fill="#222"><rect x="38" y="2" width="14" height="34" rx="6"/><rect x="38" y="54" width="14" height="34" rx="6"/><rect x="2" y="38" width="34" height="14" rx="6"/><rect x="54" y="38" width="34" height="14" rx="6"/><circle cx="45" cy="45" r="6"/></g></svg>
  <p>Doloremque laudantium, totam rem aperiam, eaqu quae ab illo inventore veritatis et quasi architecto beatae vitae dicta sunt explicabo. Nemo ipsam voluptatem quia voluptas.</p>
  <span class="btn">Read More</span>
</article>

<article class="abs card" style="left:787px">
  <svg width="314" height="402" viewBox="0 0 314 402">
    <path d="M0.5 152V28 Q154 12 313.5 0V401.5H0.5Z" fill="var(--card)" stroke="var(--line)"/>
    <path d="M0 28 Q154 12 314 0V152H0Z" fill="var(--ocean)"/>
  </svg>
  <h3 class="card-title">Mirrors Cleaning</h3>
  <svg class="icon" viewBox="0 0 90 90"><path d="M40 20v50L8 45Z" fill="none" stroke="#222" stroke-width="4" transform="matrix(-1 0 0 1 48 0)"/><path d="M50 20v50l32-25Z" fill="#222" transform="matrix(-1 0 0 1 132 0)"/></svg>
  <p>Doloremque laudantium, totam rem aperiam, eaqu quae ab illo inventore veritatis et quasi architecto beatae vitae dicta sunt explicabo. Nemo ipsam voluptatem quia voluptas.</p>
  <span class="btn">Read More</span>
</article>

<h2 class="abs about-title">About Us</h2>
<p class="abs about-text">There are many variations of passages of Lorem Ipsum available, but the majority have suffered alteration in some form, by injected humour, or randomised words which don't look even slightly believable. If you are going to use a passage of Lorem Ipsum, you need to be sure there isn't anything embarrassing hidden in the middle of text. All the Lorem Ipsum generators on the Internet tend to repeat predefined chunks as necessary, making this the first true generator on the Internet. It uses a dictionary of over 200 Latin words, combined with a handful of model sentence structures, to generate Lorem Ipsum which looks reasonable.</p>
<span class="abs btn about-btn">Read More</span>
<div class="abs video" role="img" aria-label="Video still of a hand wiping a window with a blue cloth and a spray bottle">
  <div class="abs play"><svg width="76" height="76" viewBox="0 0 76 76"><path d="M30 22v32l25-16Z" fill="#666"/></svg></div>
</div>

<h2 class="abs section-title" style="top:1621px">Our Gallery</h2>
<svg class="abs" style="left:64px;top:1776px" width="24" height="76" viewBox="0 0 24 76"><path d="M20 2L4 38l16 36" fill="none" stroke="#bbb" stroke-width="1.5"/></svg>
<div class="abs gallery-item g1" role="img" aria-label="Squeegee clearing soapy water from a window"></div>
<div class="abs gallery-item g2" role="img" aria-label="Vacuum cleaner on a polished wooden floor"></div>
<div class="abs gallery-item g3" role="img" aria-label="Bright bedroom with floor-to-ceiling windows facing the sea"></div>
<svg class="abs" style="left:1112px;top:1776px" width="24" height="76" viewBox="0 0 24 76"><path d="M4 2l16 36-16 36" fill="none" stroke="#bbb" stroke-width="1.5"/></svg>

<footer class="abs footer">
  <h4 style="left:99px">Coralbay</h4>
  <ul style="left:99px;top:104px"><li>Home</li><li>About US</li><li>Services</li><li>Gallery</li><li>Contacts</li></ul>
  <span class="divider" style="left:267px"></span>
  <h4 style="left:311px">Contact Us</h4>
  <div class="fine" style="left:311px;top:106px;font-size:13px;line-height:24px">Seagrape Lane 14<br>George Town, Grand Cayman,<br><span style="color:var(--sky)">&#9993;</span> @tidewellglasscare.ky<br><span style="color:var(--sky)">&#9742;</span> +1 345 555 0188</div>
  <span class="divider" style="left:555px"></span>
  <h4 style="left:611px">Sign to Newsletter</h4>
  <div class="fine" style="left:611px;top:108px">Join our confidential network and be the first<br>job listings for Connecticut military.</div>
  <div class="abs nl-input">Name...</div>
  <div class="abs nl-go">GO!</div>
  <span class="divider" style="left:925px"></span>
  <h4 style="left:992px">Follow Us</h4>
  <ul class="social" style="left:992px;top:112px"><li><i></i>Friendpage</li><li><i></i>chirper</li><li><i></i>clipstream</li></ul>
</footer>
<div class="abs bottombar">Impressum | Tidewell Glass Care © 2014, Alle Rechte vorbehalten</div>

</body>
</html>
```